New Business Card Design Project LORVANTI-Italy

we are LORVANTI-Italy
our company in the market for 3 years we are luxury cosmetic company and its about time for a facelift :)
i will like to have elegant luxurious and unique business card
that will give the person that get it a unique, luxurious and elegant impression
I'm VERY OPEN FOR NEW IDEAS , even duo i add a few files of things that i see on line and i like them

i add my logo as well
my website is LORVANTI.COM
(if you would like to see the main style that we have)

Target Market(s)

adult that have money :)

Industry/Entity Type

Business

Contact Information for Business Card

Name - Dario Lorvanti
Position - CEO and CO Founder
address - 4817 E Halvern
telephone - 555-384-1926
email - dario@lorvanti.com
fax - 555-384-1926
website - LORVANTI.COM

Colors
000000
959595
fbee3e
ffffff

Requirements
Must have
• big logo in GOLD color
• elegant look
• impressive
Nice to have
• not must but maybe classy pattern background
• not must but maybe emblem
• maybe clear plastic business card
Should not have
• colors
• images

```html
<!DOCTYPE html>
<html lang="en">
<head>
<meta charset="utf-8">
<title>LORVANTI Italy – Business Card</title>
<link rel="stylesheet" href="https://fonts.googleapis.com/css2?family=Cinzel:wght@500;600&family=Source+Sans+3:wght@400&display=swap">
<style>
  :root {
    --backdrop: #3b3431;
    --card: #0d0d0e;
    --card-edge: #1a1a1b;
    --silver: #c9c9c9;
    --silver-soft: #959595;
    --gold: #e2b53a;
    --gold-line: #b8912c;
  }
  * { margin: 0; padding: 0; box-sizing: border-box; }
  html, body {
    width: 1200px;
    height: 864px;
    overflow: hidden;
    background: var(--backdrop);
  }
  .stage {
    position: relative;
    width: 1200px;
    height: 864px;
  }
  .card {
    position: absolute;
    width: 520px;
    height: 300px;
    background: var(--card);
    border: 1px solid var(--card-edge);
    box-shadow: 0 18px 40px rgba(0,0,0,0.45);
  }

  /* Front */
  .card--front { left: 60px; top: 150px; }
  .brand {
    position: absolute;
    left: 0; right: 0; top: 58px;
    display: flex;
    flex-direction: column;
    align-items: center;
  }
  .brand__disc {
    width: 78px;
    height: 78px;
    border-radius: 50%;
    background: var(--silver-soft);
    margin-bottom: 18px;
  }
  .brand__name {
    font-family: "Cinzel", serif;
    font-weight: 500;
    font-size: 46px;
    letter-spacing: 1px;
    color: var(--silver);
    line-height: 1;
  }
  .brand__place {
    margin-top: 10px;
    font-family: "Cinzel", serif;
    font-weight: 500;
    font-size: 15px;
    letter-spacing: 3px;
    color: var(--silver);
  }

  /* Back */
  .card--back { left: 620px; top: 414px; }
  .holder {
    position: absolute;
    left: 34px; top: 34px;
  }
  .holder__name {
    font-family: "Cinzel", serif;
    font-weight: 600;
    font-size: 19px;
    letter-spacing: 1px;
    color: var(--gold);
  }
  .holder__title {
    margin-top: 2px;
    font-family: "Source Sans 3", sans-serif;
    font-size: 14px;
    color: var(--gold);
  }
  .contact {
    position: absolute;
    right: 30px;
    bottom: 34px;
    display: flex;
    align-items: stretch;
    font-family: "Source Sans 3", sans-serif;
    font-size: 14px;
    line-height: 1.35;
    color: var(--gold);
  }
  .contact__place { text-align: right; padding-right: 14px; padding-top: 0; }
  .contact__divider { width: 1px; background: var(--gold-line); }
  .contact__lines { padding-left: 14px; padding-top: 26px; }
</style>
</head>
<body>
  <main class="stage">
    <section class="card card--front" aria-label="Card front">
      <div class="brand">
        <div class="brand__disc"></div>
        <div class="brand__name">LORVANTI</div>
        <div class="brand__place">ITALY</div>
      </div>
    </section>

    <section class="card card--back" aria-label="Card back">
      <div class="holder">
        <div class="holder__name">DARIO LORVANTI</div>
        <div class="holder__title">CEO &amp; CO Founder</div>
      </div>
      <div class="contact">
        <div class="contact__place">
          <div>4817 E Halvern</div>
          <div>www.lorvanti.com</div>
        </div>
        <div class="contact__divider"></div>
        <div class="contact__lines">
          <div>P. 555-384-1926</div>
          <div>F. 555-384-1926</div>
          <div>E. dario@lorvanti.com</div>
        </div>
      </div>
    </section>
  </main>
</body>
</html>
```